Swiftcoinswap.com Mobile App

Swiftcoinswap.com is an online Beurea de change. They buy and sell currency from individuals and large corporations.

The app will compliment the main website of the company and focus on specific features as set out in our brief document. overall the design must be high-quality, easy navigate with a one finger operation and nice clean design.

This content is for the design of 3 screen

Loading screen
Homepage screen
Buy Currency for Branch Collection screen

attached is a full brief, but the loading screen will incorporate the logo and the home screen must allow easy navigation to 6 key button features that will enable you to go to each section of the app.

The winner will get to design the remaining screens of the app which are approx 15/18 further screens, based on the same layout.

If you can code the app as well into iPhone and Android, please make this known as well.
Updates

Hello,

For further inspritation for the Home screen, we quite like the interface on the uploaded image lumavo-home.jpg

So you slide left and right with your finger to the button, instead of a list format or something quite 2d. Almost 3d like interface maybe with an option to display all as a list?

See what sort of creativity can be achieved.

thanks

Target Market(s)

Consumers mainly aged between 25-60

Industry/Entity Type

It Company

Requirements
Must have
• good clean visually stunning appearance with apply shiny effect buttons and navigation

```html
<!DOCTYPE html>
<html lang="en">
<head>
<meta charset="utf-8">
<title>Swiftcoinswap.com – About Us</title>
<link rel="stylesheet" href="https://fonts.googleapis.com/css2?family=Bebas+Neue&family=Ubuntu:wght@400&display=swap">
<style>
  :root {
    --ink-white: #ffffff;
    --brand-red: #e3232a;
    --panel-dark: #15181f;
    --panel-edge: #050608;
    --panel-text: #f2f2f2;
    --bar-light: #5a5c60;
    --bar-dark: #1c1d20;
    --btn-light: #6c6e72;
    --btn-dark: #2a2b2e;
  }
  * { margin: 0; padding: 0; box-sizing: border-box; }
  html, body { width: 800px; height: 1200px; overflow: hidden; }
  body {
    position: relative;
    font-family: "Ubuntu", sans-serif;
    background:
      radial-gradient(ellipse 360px 320px at 470px 190px, rgba(214,196,30,0.95), rgba(214,196,30,0) 100%),
      radial-gradient(ellipse 420px 420px at 60px 420px, rgba(222,96,30,0.9), rgba(222,96,30,0) 100%),
      radial-gradient(ellipse 420px 480px at 0px 900px, rgba(40,130,210,0.95), rgba(40,130,210,0) 100%),
      radial-gradient(ellipse 500px 380px at 800px 0px, rgba(8,10,6,0.95), rgba(8,10,6,0) 100%),
      radial-gradient(ellipse 320px 320px at 0px 0px, rgba(120,20,60,0.9), rgba(120,20,60,0) 100%),
      linear-gradient(180deg, #7a4a2a 0%, #3a3560 60%, #0c1a44 100%);
  }

  .brand {
    position: absolute; left: 0; top: 250px; width: 800px;
    text-align: center; color: var(--ink-white);
  }
  .brand-name {
    display: inline-flex; align-items: center; gap: 18px;
    font-size: 76px; font-weight: 400; letter-spacing: -1px; line-height: 1;
  }
  .brand-mark {
    width: 30px; height: 30px; border-radius: 50%; background: var(--ink-white);
  }
  .brand-tagline {
    margin-top: 34px; font-size: 30px; letter-spacing: 1.5px;
  }

  .about-panel {
    position: absolute; left: 72px; top: 468px; width: 638px; height: 551px;
    background: linear-gradient(180deg, #272b33 0%, var(--panel-dark) 30%, #0f1219 100%);
    border: 2px solid var(--panel-edge); border-radius: 5px;
    box-shadow: 0 4px 14px rgba(0,0,0,0.5), inset 0 1px 0 rgba(255,255,255,0.12);
  }
  .promo-banner {
    position: absolute; left: 12px; top: 10px; width: 614px; height: 170px;
    border: 3px solid #0a0b0d;
    background: linear-gradient(90deg, #d31e24 0%, #e6e6e6 38%, #f3f3f3 70%, #c9d4e2 100%);
  }
  .panel-heading {
    position: absolute; left: 0; top: 192px; width: 100%; height: 64px;
    padding-left: 14px; line-height: 66px;
    font-family: "Bebas Neue", sans-serif; font-size: 36px; letter-spacing: 0.5px;
    color: var(--ink-white);
    border-top: 1px solid rgba(255,255,255,0.18);
    border-bottom: 1px solid rgba(255,255,255,0.18);
    background: linear-gradient(180deg, #30343c, #1e2229);
  }
  .panel-copy {
    position: absolute; left: 14px; top: 276px; width: 610px;
    font-size: 19.5px; line-height: 26.3px; color: var(--panel-text);
  }

  .tab-bar {
    position: absolute; left: 0; top: 1070px; width: 800px; height: 76px;
    background: linear-gradient(180deg, var(--bar-light) 0%, #3a3b3f 45%, var(--bar-dark) 100%);
    border-top: 1px solid #8a8c90; border-bottom: 1px solid #000;
    box-shadow: 0 -2px 8px rgba(0,0,0,0.4);
  }
  .tab-button {
    position: absolute; top: 8px; width: 62px; height: 62px; border-radius: 50%;
    background: linear-gradient(180deg, var(--btn-light), var(--btn-dark));
    border: 2px solid #111;
    box-shadow: inset 0 1px 0 rgba(255,255,255,0.3), 0 1px 0 rgba(255,255,255,0.15);
    display: flex; align-items: center; justify-content: center;
  }
  .tab-active {
    position: absolute; left: 200px; top: -9px; width: 402px; height: 92px;
    background: linear-gradient(180deg, #4a4c50 0%, #2a2b2e 50%, #141517 100%);
    border: 2px solid #000; border-radius: 5px;
    box-shadow: inset 0 1px 0 rgba(255,255,255,0.25), 0 3px 10px rgba(0,0,0,0.6);
  }
  .tab-active .tab-button { left: 12px; top: 13px; }
  .tab-label {
    position: absolute; left: 90px; right: 0; top: 0; line-height: 92px; text-align: center;
    font-family: "Bebas Neue", sans-serif; font-size: 52px; color: var(--ink-white);
    text-shadow: 0 2px 3px rgba(0,0,0,0.6);
  }
</style>
</head>
<body>
  <header class="brand">
    <div class="brand-name"><span class="brand-mark"></span>Swiftcoinswap.com</div>
    <div class="brand-tagline">CURRENCY SPECIALISTS</div>
  </header>

  <section class="about-panel">
    <div class="promo-banner" role="img" aria-label="Promotional banner: currency symbols, 0% commission offer and a smiling currency advisor"></div>
    <h1 class="panel-heading">The Leaders in Currency Exchange</h1>
    <p class="panel-copy">This is Photoshop's version &nbsp;of Lorem Ipsum. Proin gravida nibh vel velit auctor aliquet. Aenean sollicitudin, lorem quis bibendum auctor, nisi elit consequat ipsum, nec sagittis sem nibh id elit. Duis sed odio sit amet nibh vulputate cursus a sit amet mauris. Morbi accumsan ipsum velit. Nam nec tellus a odio tincidunt auctor a ornare odio. Sed non &nbsp;mauris vitae erat consequat auctor eu in elit. Class aptent taciti sociosqu ad litora torquent per conubia nostra, per inceptos himenaeos. Mauris in erat justo.</p>
  </section>

  <nav class="tab-bar">
    <div class="tab-button" style="left:40px">
      <svg width="30" height="30" viewBox="0 0 30 30"><path d="M6 4v24M6 5h14l-3 5 3 5H6" fill="none" stroke="#1a1a1a" stroke-width="3"/></svg>
    </div>
    <div class="tab-button" style="left:120px">
      <svg width="30" height="30" viewBox="0 0 30 30"><path d="M6 4v24M6 5h14l-3 5 3 5H6" fill="none" stroke="#1a1a1a" stroke-width="3"/></svg>
    </div>
    <div class="tab-active">
      <div class="tab-button">
        <svg width="30" height="34" viewBox="0 0 30 34"><rect x="4" y="2" width="22" height="30" rx="2" fill="#eee"/><circle cx="15" cy="13" r="4" fill="#333"/><path d="M8 25c1-5 13-5 14 0z" fill="#333"/><path d="M2 7h4M2 13h4M2 19h4M2 25h4" stroke="#eee" stroke-width="2"/></svg>
      </div>
      <div class="tab-label">About Us</div>
    </div>
    <div class="tab-button" style="left:630px">
      <svg width="30" height="30" viewBox="0 0 30 30"><path d="M6 4v24M6 5h14l-3 5 3 5H6" fill="none" stroke="#1a1a1a" stroke-width="3"/></svg>
    </div>
    <div class="tab-button" style="left:713px">
      <svg width="30" height="30" viewBox="0 0 30 30"><path d="M6 4v24M6 5h14l-3 5 3 5H6" fill="none" stroke="#1a1a1a" stroke-width="3"/></svg>
    </div>
  </nav>
</body>
</html>
```